Business Card Design for a new Senior Concierge Business 1.3.24

I need a professional business card to handout at networking events for my senior helper business. I would like to use the logo I have uploaded. The design should be clear and easy to read and should list the following information...
Delia Parkhurst
Owner
www.HarborlightElderAides.com
Larkmoor, Texas
936.482.5079
Delia@harborlightelderaides.com

Target Market(s)

Senior Citizens

Industry/Entity Type

Personal Helper/ Assisstant

Contact Information for Business Card

I have included the details in the project description box.

Font styles to use
Serif

Colors
0054AA
0677BA
7BADD7
CADEEF
E8F1F8
59FF00
82FF00
B8FF75
E3FFCB
F4FFEA
E54698
E96AAD
F1A4CE
F9D9EA
FCEFF6
6B429C
8869AF
B7A5CE
E3DAEB
F3F0F8

Requirements
Must have
• Include uploaded logo
Nice to have
• The log that has been uploaded
Should not have
• No crazy fonts

```html
<!DOCTYPE html>
<html lang="en">
<head>
<meta charset="utf-8">
<title>Harborlight Elder Aides – Business Card</title>
<link href="https://fonts.googleapis.com/css2?family=Anton&family=Lato:wght@400;700&display=swap" rel="stylesheet">
<style>
  :root {
    --backdrop: #2b2b2b;
    --card: #ffffff;
    --violet: #6330e8;
    --rose: #d81e5b;
    --teal: #008b8f;
    --ink: #1c1c1c;
  }
  * { margin: 0; padding: 0; box-sizing: border-box; }
  html, body {
    width: 1047px; height: 1200px; overflow: hidden;
    background: var(--backdrop);
  }
  .canvas { position: relative; width: 1047px; height: 1200px; }
  .card {
    position: absolute; left: 156px; width: 743px; height: 424px;
    background: var(--card); border-radius: 22px; overflow: hidden;
  }
  .card--front { top: 120px; }
  .card--back { top: 634px; }
  .card__wave { position: absolute; inset: 0; width: 100%; height: 100%; }

  .holder { position: absolute; left: 32px; top: 208px; }
  .holder__name {
    font-family: "Anton", sans-serif; font-size: 36px; letter-spacing: 2px;
    color: var(--violet); text-transform: uppercase; line-height: 1.1;
  }
  .holder__role {
    font-family: "Lato", sans-serif; font-size: 20px; color: var(--rose);
    margin-top: 2px;
  }
  .contact { position: absolute; left: 32px; top: 292px; list-style: none; }
  .contact__item {
    display: flex; align-items: center; gap: 10px; height: 26.5px;
    font-family: "Lato", sans-serif; font-size: 17.5px; color: var(--ink);
  }
  .contact__item--phone { font-size: 20px; }
  .contact__icon { width: 18px; height: 18px; flex: none; fill: var(--teal); }

  .brand-mark {
    position: absolute; left: 340px; top: 150px; width: 300px;
    text-align: center; font-family: "Lato", sans-serif; font-weight: 700;
    font-size: 30px; line-height: 1.25; color: var(--rose);
  }

  .brand {
    position: absolute; inset: 0; display: flex; align-items: center;
    justify-content: center; gap: 16px;
  }
  .brand__dot { width: 38px; height: 38px; border-radius: 50%; background: var(--rose); }
  .brand__name {
    font-family: "Lato", sans-serif; font-weight: 400; font-size: 46px;
    color: var(--violet);
  }
</style>
</head>
<body>
<main class="canvas">
  <section class="card card--front">
    <svg class="card__wave" viewBox="0 0 770 439" preserveAspectRatio="none" aria-hidden="true">
      <path fill="var(--violet)" d="M650 0 L770 0 L770 439 L545 439 C545 400 560 370 610 340 C700 290 760 240 765 170 C770 90 720 30 650 0 Z"/>
    </svg>

    <p class="brand-mark">Harborlight<br>Elder Aides</p>

    <div class="holder">
      <h1 class="holder__name">Delia Parkhurst</h1>
      <p class="holder__role">Owner</p>
    </div>

    <ul class="contact">
      <li class="contact__item contact__item--phone">
        <svg class="contact__icon" viewBox="0 0 24 24"><path d="M6.6 10.8a15 15 0 0 0 6.6 6.6l2.2-2.2a1 1 0 0 1 1-.25 11.4 11.4 0 0 0 3.6.57 1 1 0 0 1 1 1V20a1 1 0 0 1-1 1A17 17 0 0 1 3 4a1 1 0 0 1 1-1h3.5a1 1 0 0 1 1 1c0 1.25.2 2.45.57 3.57a1 1 0 0 1-.25 1z"/></svg>
        936.482.5079
      </li>
      <li class="contact__item">
        <svg class="contact__icon" viewBox="0 0 24 24"><path d="M2 5h20v14H2z M4 7v.4l8 5 8-5V7z" fill-rule="evenodd"/></svg>
        Delia@harborlightelderaides.com
      </li>
      <li class="contact__item">
        <svg class="contact__icon" viewBox="0 0 24 24"><circle cx="12" cy="12" r="10"/><path d="M2 12h20M12 2c3 3 3 17 0 20M12 2c-3 3-3 17 0 20" stroke="#fff" stroke-width="1.5" fill="none"/></svg>
        www.HarborlightElderAides.com
      </li>
      <li class="contact__item">
        <svg class="contact__icon" viewBox="0 0 24 24"><path d="M12 2a7 7 0 0 0-7 7c0 5 7 13 7 13s7-8 7-13a7 7 0 0 0-7-7zm0 9.5A2.5 2.5 0 1 1 12 6.5a2.5 2.5 0 0 1 0 5z"/></svg>
        Larkmoor, Texas
      </li>
    </ul>
  </section>

  <section class="card card--back">
    <div class="brand">
      <span class="brand__dot" aria-hidden="true"></span>
      <p class="brand__name">Harborlight Elder Aides</p>
    </div>
  </section>
</main>
</body>
</html>
```